Business Card - Tidal Lanes

Need Business Card design for company named Tidal Lanes. Software development focused mainly on Brindle Orvix & Zelt Apps. I've attached our logo with both a black and white background. Please add trademark symbol to logo when using.

```html
<!DOCTYPE html>
<html lang="en">
<head>
<meta charset="utf-8">
<title>Tidal Lanes – Business Card</title>
<link rel="stylesheet" href="https://fonts.googleapis.com/css2?family=Source+Sans+3:wght@400;600;700&display=swap">
<style>
  :root {
    --bg: #e9eaee;
    --black: #0b0b0b;
    --red: #d92128;
    --yellow: #f7c11a;
    --orange: #f59c33;
    --white: #ffffff;
    --ink: #1a1a1a;
  }
  * { box-sizing: border-box; margin: 0; padding: 0; }
  html, body { width: 1200px; height: 987px; overflow: hidden; }
  body {
    background: var(--bg);
    font-family: "Source Sans 3", "Helvetica Neue", Arial, sans-serif;
    position: relative;
  }
  .card {
    position: absolute;
    width: 700px;
    height: 400px;
    border-radius: 28px;
    overflow: hidden;
    left: 250px;
    box-shadow: 0 6px 18px rgba(0,0,0,.12);
  }
  /* Front */
  .card-front { top: 50px; background: var(--black); }
  .band { position: absolute; left: 0; width: 100%; }
  .band-red { top: 190px; height: 136px; background: var(--red); }
  .band-gold { top: 326px; height: 50px; background: linear-gradient(90deg, var(--yellow), var(--orange)); }
  .band-base { top: 376px; height: 24px; background: var(--red); }
  .brand {
    position: absolute; top: 92px; left: 0; width: 100%;
    text-align: center; color: var(--white);
    font-weight: 700; font-size: 46px; letter-spacing: -0.5px;
  }
  .brand sup { font-size: 14px; vertical-align: super; }
  .contact {
    position: absolute; top: 214px; left: 0; width: 100%;
    display: flex; justify-content: center; align-items: center;
    color: var(--white); font-size: 25px; line-height: 1.2;
  }
  .address { text-align: right; padding-right: 26px; }
  .divider { width: 2px; height: 70px; background: rgba(255,255,255,.85); }
  .phones { padding-left: 26px; }
  .phone-line { display: flex; align-items: center; gap: 12px; }
  .phone-line svg { width: 20px; height: 22px; fill: var(--white); }
  .holder {
    position: absolute; top: 330px; left: 60px;
    font-size: 28px; color: var(--ink);
  }
  .holder strong { font-weight: 700; }
  /* Back */
  .card-back {
    top: 537px;
    background: linear-gradient(120deg, var(--yellow), var(--orange));
  }
  .back-brand {
    position: absolute; top: 130px; left: 0; width: 100%;
    text-align: center; color: var(--white);
    font-weight: 700; font-size: 72px; letter-spacing: -1px;
  }
  .back-brand sup { font-size: 20px; vertical-align: super; }
  .website {
    position: absolute; top: 250px; left: 0; width: 100%;
    text-align: center; color: var(--white);
    font-size: 22px; letter-spacing: 2px;
  }
</style>
</head>
<body>
  <section class="card card-front">
    <div class="band band-red"></div>
    <div class="band band-gold"></div>
    <div class="band band-base"></div>

    <div class="brand">Tidal Lanes<sup>™</sup></div>

    <div class="contact">
      <div class="address">4420 Harbor Row<br>Corvale, FL 30917</div>
      <div class="divider"></div>
      <div class="phones">
        <div class="phone-line">
          <svg viewBox="0 0 20 22" aria-hidden="true"><rect x="4" y="0" width="12" height="22" rx="2"/><rect x="6" y="3" width="8" height="8" fill="#d92128"/><circle cx="10" cy="17" r="1.6" fill="#d92128"/></svg>
          <span>555-204-7316</span>
        </div>
        <div class="phone-line">
          <svg viewBox="0 0 22 22" aria-hidden="true"><path d="M2 8c0-3 4-5 9-5s9 2 9 5v2h-5V8c-2-.8-6-.8-8 0v2H2z"/><rect x="4" y="12" width="14" height="9" rx="2"/></svg>
          <span>555-381-6042</span>
        </div>
      </div>
    </div>

    <div class="holder"><strong>Your Name,</strong> Title</div>
  </section>

  <section class="card card-back">
    <div class="back-brand">Tidal Lanes<sup>™</sup></div>
    <div class="website">www.tidallanes.com</div>
  </section>
</body>
</html>
```